Modern Business Card For A Digital Advertising Company

I'll be print on the Pell Prints Velour paper http://us.pellprints.com/products/velour/business-cards.html
Need's to be modern and use the color palette of the logo or gray scales. I think integrating the pixelation of the logo in to the card and having it wrap from one side to the other could be interesting. My company provides ad operations, web development, and number of other services to websites around the world. You can see my website at http://www.zantorhq.com
Contact info on the card needs to have
Owen Lasko
President
p.318.204.6637
owen@zantorhq.com
http://www.zantorhq.com
Doesn't necessarily need to be in that order
Website owners
Business

```html
<!DOCTYPE html>
<html lang="en">
<head>
<meta charset="utf-8">
<title>Zantor HQ — Business Card</title>
<link rel="stylesheet" href="https://fonts.googleapis.com/css2?family=Open+Sans:wght@400;700&display=swap">
<style>
  :root {
    --backdrop: #000000;
    --card: #ffffff;
    --card-edge: #9a9a9a;
    --green: #8dc63f;
    --ink: #4a4a48;
    --text: #222222;
    --rule: #111111;
  }
  * { margin: 0; padding: 0; box-sizing: border-box; }
  html, body { width: 900px; height: 1200px; overflow: hidden; background: var(--backdrop); }
  body { position: relative; font-family: "Open Sans", Arial, sans-serif; }

  .card {
    position: absolute;
    width: 782px;
    height: 448px;
    background: var(--card);
    border: 2px solid var(--card-edge);
    border-radius: 30px;
    overflow: hidden;
  }
  .card--front { left: 57px; top: 121px; }
  .card--back  { left: 60px; top: 628px; }

  .card__wave { position: absolute; inset: 0; width: 100%; height: 100%; }
  .wave-black { fill: var(--rule); }
  .wave-green { fill: var(--green); stroke: var(--card); stroke-width: 5; }

  .brand {
    position: absolute;
    display: flex;
    align-items: center;
    gap: 12px;
    color: var(--green);
    font-weight: 700;
    letter-spacing: 2px;
    white-space: nowrap;
  }
  .brand__mark { display: block; background: var(--green); }
  .card--front .brand { left: 312px; top: 185px; font-size: 40px; }
  .card--front .brand__mark { width: 30px; height: 30px; }
  .card--back .brand { left: 124px; top: 170px; font-size: 36px; }
  .card--back .brand__mark { width: 26px; height: 26px; }

  .person { position: absolute; right: 44px; top: 38px; text-align: right; color: var(--ink); }
  .person__name { font-size: 29px; font-weight: 700; line-height: 1.1; }
  .person__title { font-size: 20px; color: var(--text); line-height: 1.3; }

  .divider { position: absolute; left: 449px; top: 160px; width: 2px; height: 162px; background: var(--rule); }

  .contact { position: absolute; left: 466px; top: 194px; list-style: none; }
  .contact li { display: flex; align-items: center; gap: 10px; height: 35px; font-size: 20px; color: var(--text); }
  .contact svg { width: 22px; height: 22px; flex: none; }
  .icon { fill: none; stroke: var(--green); stroke-width: 1.6; }
</style>
</head>
<body>

<section class="card card--front">
  <svg class="card__wave" viewBox="0 0 782 448" preserveAspectRatio="none" aria-hidden="true">
    <path class="wave-black" d="M0,342 C180,318 330,352 470,352 C620,352 720,330 782,298 L782,448 L0,448 Z"/>
    <path class="wave-green" d="M0,376 C180,350 330,372 470,372 C620,372 720,356 782,328 L782,470 L0,470 Z"/>
  </svg>
  <div class="brand"><span class="brand__mark"></span>ZANTOR HQ</div>
</section>

<section class="card card--back">
  <svg class="card__wave" viewBox="0 0 782 448" preserveAspectRatio="none" aria-hidden="true">
    <path class="wave-black" d="M0,296 C90,328 220,344 380,338 C560,332 700,338 782,350 L782,448 L0,448 Z"/>
    <path class="wave-green" d="M0,320 C90,352 220,364 380,360 C560,356 700,360 782,368 L782,470 L0,470 Z"/>
  </svg>

  <div class="brand"><span class="brand__mark"></span>ZANTOR HQ</div>

  <div class="person">
    <p class="person__name">Owen Lasko</p>
    <p class="person__title">President</p>
  </div>

  <div class="divider"></div>

  <ul class="contact">
    <li>
      <svg viewBox="0 0 22 22" aria-hidden="true"><circle class="icon" cx="11" cy="11" r="9"/><path class="icon" d="M8,6 l2,3 -1.5,1.5 c0.8,1.6 1.8,2.6 3.4,3.4 L13.4,12.4 l3,2 -1.5,2 C10,16 6,12 6.2,7.6 Z"/></svg>
      318-204-6637
    </li>
    <li>
      <svg viewBox="0 0 22 22" aria-hidden="true"><rect class="icon" x="2.5" y="5" width="17" height="12"/><path class="icon" d="M2.5,5 L11,12 19.5,5 M2.5,17 L9,11 M19.5,17 L13,11"/></svg>
      owen@zantorhq.com
    </li>
    <li>
      <svg viewBox="0 0 22 22" aria-hidden="true"><circle class="icon" cx="11" cy="11" r="9"/><ellipse class="icon" cx="11" cy="11" rx="4" ry="9"/><path class="icon" d="M2,11 H20 M4,6.5 H18 M4,15.5 H18"/></svg>
      www.zantorhq.com
    </li>
  </ul>
</section>

</body>
</html>
```